KIRO Nature Soap

We need to design new product Nature and medicative Soap.Made in Malaysia
* 100% natural.
* made from nature Tropic oil.
* Very effective for Acne & Skin irritation
* size 100 Gm.
* Use for all skin types including sensitive skin
* Name of the product " KIRO Soap"

Reason: please I need to extended since I haven't receive any suitable design for my project

Target Market(s)

International

Industry/Entity Type

Hair And Beauty

Font styles to use
Serif

Colors
33a6d7
abd037
fbed22

Requirements
Must have
• * must have English- Arabic ingredient
• * Very effective for Acne & Skin irritation
Nice to have
• * some things related to natural (water,tree,face..)
• * Show faces picture (after - before)

```html
<!DOCTYPE html>
<html lang="en">
<head>
<meta charset="utf-8">
<title>KIRO Soap – Tube Label</title>
<link href="https://fonts.googleapis.com/css2?family=Marcellus&family=PT+Sans:wght@700&display=swap" rel="stylesheet">
<style>
  :root {
    --bg: #dfe5e8;
    --seal-yellow: #e4dc2a;
    --wave-teal: #2a9fb8;
    --wave-green: #8fcf7a;
    --wave-aqua: #6fc9cf;
    --ink-white: #ffffff;
    --ink-navy: #0d2a3c;
  }
  html, body {
    margin: 0;
    width: 1200px;
    height: 848px;
    overflow: hidden;
    background: var(--bg);
  }
  .canvas {
    position: relative;
    width: 1200px;
    height: 848px;
  }
  .label {
    position: absolute;
    top: 130px;
    width: 340px;
    height: 580px;
    overflow: hidden;
    box-shadow: 0 10px 30px rgba(0,0,0,0.15);
  }
  .label--front { left: 240px; }
  .label--back { left: 620px; }
  .label__seal {
    height: 16px;
    background: var(--seal-yellow);
  }
  .label__pattern {
    position: absolute;
    top: 16px; left: 0; right: 0; bottom: 0;
    background: linear-gradient(160deg, var(--wave-aqua) 0%, var(--wave-green) 35%, var(--wave-teal) 65%, var(--wave-green) 100%);
  }
  .label__content {
    position: absolute;
    top: 16px; left: 0; right: 0; bottom: 0;
    text-align: center;
    color: var(--ink-white);
    font-family: "Marcellus", serif;
  }
  .brand-mark {
    margin-top: 70px;
    display: flex;
    flex-direction: column;
    align-items: center;
    gap: 8px;
  }
  .brand-mark__dot {
    width: 44px; height: 44px;
    border-radius: 50%;
    background: var(--ink-white);
  }
  .brand-mark__name {
    font-size: 14px;
    letter-spacing: 2px;
  }
  .product-name {
    margin: 70px 0 0;
    font-weight: 400;
    line-height: 1;
    text-shadow: 0 2px 3px rgba(0,0,0,0.35);
  }
  .product-name__brand { display: block; font-size: 68px; }
  .product-name__type { display: block; font-size: 56px; margin-top: 4px; }
  .net-weight {
    margin-top: 90px;
    font-size: 22px;
    font-family: "PT Sans", sans-serif;
    font-weight: 700;
  }
  .origin {
    margin-top: 38px;
    font-size: 15px;
    font-family: "PT Sans", sans-serif;
    font-weight: 700;
  }
  .claims {
    position: absolute;
    top: 100px; left: 34px; right: 20px;
    margin: 0; padding: 0;
    list-style: none;
    text-align: left;
    color: var(--ink-navy);
    font-family: "PT Sans", sans-serif;
    font-weight: 700;
    font-size: 17px;
    line-height: 39px;
  }
</style>
</head>
<body>
<main class="canvas">
  <section class="label label--front">
    <div class="label__seal"></div>
    <div class="label__pattern" role="img" aria-label="Flowing teal and green wave pattern"></div>
    <div class="label__content">
      <div class="brand-mark">
        <span class="brand-mark__dot"></span>
        <span class="brand-mark__name">KIRO</span>
      </div>
      <h1 class="product-name">
        <span class="product-name__brand">KIRO</span>
        <span class="product-name__type">Soap</span>
      </h1>
      <div class="net-weight">100 Gm</div>
      <div class="origin">Made in Malaysia</div>
    </div>
  </section>

  <section class="label label--back">
    <div class="label__seal"></div>
    <div class="label__pattern" role="img" aria-label="Flowing teal and green wave pattern"></div>
    <ul class="claims">
      <li>Made from nature Tropic oil.</li>
      <li>Very effective for</li>
      <li>Acne &amp; Skin irritation</li>
      <li>Use for all skin types</li>
      <li>including sensitive skin</li>
    </ul>
  </section>
</main>
</body>
</html>
```